Velundra Jobs portal

Velundra Jobs is a job portal connecting job seekers and companies offering part time jobs in the Mena region, starting in the UAE. We would like to see designs that use the color blue. We have attached images to give an idea what the website should look like. When a company posts a job the job seekers are not allowed to see which company has posted a job. There should also be a coinvex gateway. On the landing page we want a catching picture that we will send.

Target Market(s)

Students and promotional workers

Logo Text

Velundra Jobs

Coding

Coded - Design and coding required

Number of Pages Required

4 page

Font styles to use
Sans Serif

Colors
33a6d7
0692cd
85cae6

```html
<!DOCTYPE html>
<html lang="en">
<head>
<meta charset="utf-8">
<title>Velundra Jobs – Landing</title>
<link href="https://fonts.googleapis.com/css2?family=Open+Sans:wght@400;600&display=swap" rel="stylesheet">
<style>
  :root {
    --teal-light: #86e2e3;
    --teal-dark: #5f9a91;
    --blue-light: #4e88df;
    --blue-dark: #3a6bbb;
    --brand-blue: #3264b0;
    --brand-teal: #4fc3c4;
    --brand-pink: #e24b8c;
    --text-grey: #9a9a9a;
    --text-dark: #444;
    --white: #fff;
  }
  * { margin: 0; padding: 0; box-sizing: border-box; }
  html, body { width: 1200px; height: 797px; overflow: hidden; }
  body {
    position: relative;
    font-family: "Open Sans", Arial, sans-serif;
    background: linear-gradient(180deg, var(--blue-light), var(--blue-dark));
  }
  .backdrop-teal {
    position: absolute; inset: 0;
    background: linear-gradient(180deg, var(--teal-light), var(--teal-dark));
    clip-path: polygon(0 0, 617px 0, 495px 797px, 0 797px);
  }
  .page-shadow {
    position: absolute; left: 107px; top: 45px; width: 1003px; height: 690px;
    background: rgba(255,255,255,0.45);
  }
  .page {
    position: absolute; left: 99px; top: 52px; width: 1002px; height: 691px;
    background: var(--white);
  }
  .accent-strip {
    display: flex; height: 4px;
  }
  .accent-strip span { flex: 1; }
  .accent-strip .blue { background: var(--brand-blue); }
  .accent-strip .pink { background: var(--brand-pink); }
  .accent-strip .teal { background: var(--brand-teal); }
  .mascot-area {
    position: absolute; left: 291px; top: 184px; width: 130px; height: 168px;
    border-radius: 8px;
    background: linear-gradient(160deg, #5ec6c8, #3264b0 60%, #e24b8c);
    opacity: 0.85;
  }
  .brand-name {
    position: absolute; left: 250px; top: 360px; width: 214px;
    text-align: center;
    font-size: 40px; font-weight: 400; color: var(--brand-teal);
    letter-spacing: 0.5px;
  }
  .intro {
    position: absolute; left: 542px; top: 191px; width: 236px;
    font-size: 12px; line-height: 16.3px; color: var(--text-grey);
    text-align: justify;
  }
  .join-button {
    position: absolute; left: 543px; top: 335px; width: 234px; height: 44px;
    background: var(--brand-blue); color: var(--white);
    font-size: 20.5px; line-height: 44px; text-align: center;
    border-radius: 2px;
  }
  .signin-note {
    position: absolute; left: 543px; top: 387px; width: 234px;
    text-align: center; font-size: 12px; color: var(--text-dark);
  }
  .signin-note a { color: var(--brand-blue); }
  .divider {
    position: absolute; left: 72px; top: 598px; width: 858px;
    border-top: 1px dotted #cfcfcf;
  }
  .page-code {
    position: absolute; left: 963px; top: 590px; font-size: 12px; color: #222;
  }
  .copyright {
    position: absolute; left: 164px; top: 645px; font-size: 11.5px; color: var(--text-dark);
  }
  .footer-links {
    position: absolute; right: 114px; top: 645px; font-size: 11.5px; color: var(--text-dark);
    display: flex; gap: 13px;
  }
</style>
</head>
<body>
  <div class="backdrop-teal"></div>
  <div class="page-shadow"></div>
  <main class="page">
    <div class="accent-strip"><span class="blue"></span><span class="pink"></span><span class="teal"></span></div>
    <div class="mascot-area" role="img" aria-label="Brand mascot illustration"></div>
    <div class="brand-name">Velundra</div>
    <p class="intro">We are providing part dolor sit amet, consectetur adipiscing elit. Aenean ultrices elementum ornare. Curabitur congue pretium augue. Vestibulum tristique, justo bibendum cursus fermentum, elit mauris porta justo, a sollicitudin leo eros sit amet augue. Etiam Right place</p>
    <div class="join-button">Join Velundra</div>
    <p class="signin-note">for our users you can <a href="#">Sign In</a></p>
    <div class="divider"></div>
    <div class="page-code">M3</div>
    <p class="copyright">Copyrights reserved to velundra 2015</p>
    <nav class="footer-links"><span>About Us</span><span>|</span><span>Terms and conditions</span><span>|</span><span>Sitemap</span></nav>
  </main>
</body>
</html>
```